Corporate Business Card

Very professional, Modern, Not to busy, include phone address email, website
(253) 617-4930, 18761 52nd Avenue S, Kent, WA 98047, martin@plumlinegroup.com, varkoworks.com

Target Market(s)

Manufacturing

Industry/Entity Type

Aero, machining, manufacturing, Off road racing

Contact Information for Business Card

Phone, address email, website

```html
<!DOCTYPE html>
<html lang="en">
<head>
<meta charset="utf-8">
<title>Varko Works – Business Card</title>
<link rel="stylesheet" href="https://fonts.googleapis.com/css2?family=Russo+One&family=Lato:wght@400;700&display=swap">
<style>
  :root {
    --navy: #1b3770;
    --red: #d3232b;
    --white: #ffffff;
    --ink: #3a3a3a;
    --stage: #2b2c2e;
  }
  * { box-sizing: border-box; margin: 0; padding: 0; }
  html, body { width: 1200px; height: 786px; overflow: hidden; }
  body {
    background: var(--stage);
    font-family: "Lato", Arial, sans-serif;
    position: relative;
  }
  .card {
    position: absolute;
    top: 238px;
    width: 540px;
    height: 309px;
    overflow: hidden;
  }
  .card--front { left: 40px; background: var(--navy); }
  .card--back { left: 620px; background: var(--white); }

  /* front */
  .front-logo {
    position: absolute;
    left: 150px;
    top: 112px;
    font-family: "Russo One", Arial, sans-serif;
    font-size: 44px;
    letter-spacing: 1px;
    color: var(--white);
    white-space: nowrap;
  }
  .front-rule {
    position: absolute;
    left: 80px;
    top: 196px;
    width: 240px;
    height: 2px;
    background: var(--white);
  }

  /* back */
  .edge { position: absolute; }
  .back-logo {
    position: absolute;
    right: 40px;
    top: 48px;
    font-family: "Russo One", Arial, sans-serif;
    font-size: 26px;
    color: var(--navy);
    white-space: nowrap;
  }
  .back-rule {
    position: absolute;
    left: 70px;
    top: 126px;
    width: 370px;
    height: 2px;
    background: var(--navy);
  }
  .holder { position: absolute; left: 60px; top: 72px; }
  .holder-name {
    font-family: "Russo One", Arial, sans-serif;
    font-size: 22px;
    color: var(--navy);
    letter-spacing: 0.5px;
    line-height: 1;
  }
  .holder-title {
    font-size: 15px;
    color: var(--red);
    margin-top: 4px;
    margin-left: 14px;
  }
  .contacts {
    position: absolute;
    left: 60px;
    bottom: 34px;
    list-style: none;
    font-size: 13px;
    color: var(--ink);
  }
  .contacts li { display: flex; align-items: center; gap: 8px; line-height: 20px; }
  .contacts svg { width: 11px; height: 11px; fill: var(--navy); flex: none; }
  .address {
    position: absolute;
    right: 48px;
    top: 160px;
    text-align: right;
    font-size: 13px;
    line-height: 19px;
    color: var(--ink);
    font-style: normal;
  }
</style>
</head>
<body>

<section class="card card--front" aria-label="Card front">
  <div class="front-logo">VARKO WORKS</div>
  <div class="front-rule"></div>
</section>

<section class="card card--back" aria-label="Card back">
  <svg class="edge" width="540" height="309" viewBox="0 0 540 309" aria-hidden="true">
    <polygon points="0,40 8,40 8,250 0,262" fill="var(--red)"/>
    <polygon points="532,0 540,0 540,150 532,138" fill="var(--navy)"/>
  </svg>

  <div class="back-logo">VARKO WORKS</div>

  <div class="holder">
    <h1 class="holder-name">DANIEL BROOKS</h1>
    <p class="holder-title">Managing Director</p>
  </div>
  <div class="back-rule"></div>

  <address class="address">18761 52nd Avenue S<br>Kent, WA 98047</address>

  <ul class="contacts">
    <li>
      <svg viewBox="0 0 24 24"><path d="M6.6 10.8a15 15 0 0 0 6.6 6.6l2.2-2.2c.3-.3.7-.4 1-.2 1.1.4 2.3.6 3.6.6.6 0 1 .4 1 1V20c0 .6-.4 1-1 1A17 17 0 0 1 3 4c0-.6.4-1 1-1h3.5c.6 0 1 .4 1 1 0 1.3.2 2.5.6 3.6.1.3 0 .7-.2 1z"/></svg>
      (253) 617-4930
    </li>
    <li>
      <svg viewBox="0 0 24 24"><path d="M2 5h20v14H2zm2 2v.5l8 5 8-5V7z"/></svg>
      martin@plumlinegroup.com
    </li>
    <li>
      <svg viewBox="0 0 24 24"><circle cx="12" cy="12" r="10"/></svg>
      www.varkoworks.com
    </li>
  </ul>
</section>

</body>
</html>
```